Retro Label for old fashioned soda

We need a label for soda we are having private labeled for our retro, 1950's ice cream shop www.maplefrostparlor.example I don't want the label to look like something from 2017 with a retro feel, but more like an original (possibly kinda cheesy) label you'd see from the 1950's with some of the old catch lines like "tastes great", "invigorating" or "it is refreshing!" The prominent brand should be the name of our ice cream shop, Maple Frost Parlor. the soda is also pure cane sugar so it might be good to have that on somewhere

Label size is 2.4" wide by 4" tall. Here is an example of some retro labels from findwell. I attached on file to this contest but there are more here: https://www.findwell.example/images?q=retro+soda+label&ref=Kx7Qm2Lp9Vt4Rz8Nw3Hd5Jb6Yc1Fg0TsUaWe2Pv7Xo4Ml9Qn8Bk3Dr6Zh5Cy1Ej0Gu7Ai4Ot2Sf9Lw6Nx8Mb3&w=2560&h=1470#img=Pq7Rt2Vw9Xz4Ab:

The label will be the same for all the flavors with the exception of the flavor name changing somewhere on the label. These are the flavors

Root Beer
Orange
Black Cherry
Lemonade
Raspberry Lime -Rickey
White Birch Beer
Lemon Iced Tea
Vanilla Cream
Orange Cream
Sarsaparilla
Ginger Ale

Industry/Entity Type

Shop

Colors

Designer to choose colors to be used in the design.

Requirements
Must have
• retro feel. authentic old fashioned look

```html
<!DOCTYPE html>
<html lang="en">
<head>
<meta charset="utf-8">
<title>Maple Frost Parlor – Vanilla Cream Soda Label</title>
<link rel="stylesheet" href="https://fonts.googleapis.com/css2?family=Lobster&family=Parisienne&family=Josefin+Sans:wght@600&family=Righteous&display=swap">
<style>
  :root {
    --page: #ffffff;
    --cream: #fdecc9;
    --soda-red: #f50f23;
    --ink: #1a1a1a;
    --trim-green: #5c9c78;
  }
  html, body {
    margin: 0;
    width: 1200px;
    height: 1200px;
    overflow: hidden;
    background: var(--page);
  }
  .canvas {
    position: relative;
    width: 1200px;
    height: 1200px;
  }
  .soda-label {
    position: absolute;
    left: 270px;
    top: 72px;
    width: 660px;
    height: 1056px;
    filter: drop-shadow(6px 10px 10px rgba(0,0,0,0.22));
  }
  .label-paper { fill: var(--cream); }
  .label-trim { fill: none; stroke: var(--trim-green); stroke-width: 3.5; }
  .label-red-field { fill: var(--soda-red); }
  .tagline-box, .sugar-band { fill: var(--cream); }
  .tagline {
    font-family: "Parisienne", cursive;
    font-size: 40px;
    fill: var(--ink);
  }
  .brand-name {
    font-family: "Lobster", cursive;
    font-size: 84px;
    fill: var(--ink);
  }
  .sugar-claim {
    font-family: "Josefin Sans", sans-serif;
    font-weight: 600;
    font-size: 38px;
    fill: var(--ink);
  }
  .flavor-name {
    font-family: "Righteous", sans-serif;
    font-size: 118px;
    fill: var(--ink);
  }
</style>
</head>
<body>
<main class="canvas">
  <svg class="soda-label" viewBox="0 0 600 960" xmlns="http://www.w3.org/2000/svg" aria-label="Maple Frost Parlor vanilla cream soda label">
    <rect class="label-paper" x="0" y="0" width="600" height="960"/>
    <rect class="label-trim" x="27" y="27" width="546" height="906" rx="14"/>

    <polygon class="label-red-field" points="40,40 562,40 562,560 40,705"/>
    <rect class="tagline-box" x="53" y="53" width="495" height="82"/>
    <text class="tagline" x="300" y="108" text-anchor="middle">it tastes great !</text>

    <text class="brand-name" x="305" y="300" text-anchor="middle">Maple Frost</text>
    <text class="brand-name" x="305" y="420" text-anchor="middle">Parlor</text>

    <polygon class="sugar-band" points="53,590 548,450 548,548 53,683"/>
    <text class="sugar-claim" x="307" y="583" text-anchor="middle" transform="rotate(-15.6 307 570)">PURE CANE SUGAR</text>

    <text class="flavor-name" x="310" y="795" text-anchor="middle" textLength="400" lengthAdjust="spacingAndGlyphs">vanilla</text>
    <text class="flavor-name" x="308" y="896" text-anchor="middle" textLength="405" lengthAdjust="spacingAndGlyphs">cream</text>
  </svg>
</main>
</body>
</html>
```